Ward Compass Business Card Design*

We need a business card design for our company Ward Compass. Our company is specialized in providing online consulting services regarding medical institutions, hospitals and doctors. We work with patients worldwide looking to choose between healthcare providers. We have a website you may use as a reference, where we list doctors and clinics worldwide. So we target Medical providers as well as patients worldwide.
Target Market(s)
Medical Providers and patients around the world
Industry/Entity Type
Medical
Contact Information for Business Card
Salwa Kettani
CEO
+90 612 348 2175
info@wardcompass.example
www.wardcompass.example
14 Annakhil 7 H.R.B. Rabat, Morocco
Requirements
Must have
- Company logo/name on one full side, personal info and smaller logo and company name on the other side.
Nice to have
- Smart and elegant design

```html
<!DOCTYPE html>
<html lang="en">
<head>
<meta charset="utf-8">
<title>Ward Compass — Business Card</title>
<link rel="stylesheet" href="https://fonts.googleapis.com/css2?family=Montserrat:wght@400;500;600;700&display=swap">
<style>
  :root {
    --page-bg: #e9e7e3;
    --brand-blue: #2c4a7e;
    --brand-blue-deep: #243f6d;
    --card-white: #f7f7f8;
    --ink-grey: #8a8f99;
    --rule-grey: #c9ccd2;
    --soft-white: #eef1f6;
  }
  * { margin: 0; padding: 0; box-sizing: border-box; }
  html, body {
    width: 900px; height: 1200px; overflow: hidden;
    background: var(--page-bg);
    font-family: "Montserrat", Arial, sans-serif;
  }
  .canvas { position: relative; width: 900px; height: 1200px; }
  .card {
    position: absolute; left: 84px; width: 732px; height: 450px;
    box-shadow: 0 6px 18px rgba(0,0,0,0.18);
  }
  .card-front { top: 126px; background: var(--brand-blue); }
  .card-back { top: 621px; background: var(--card-white); }

  .front-brand {
    position: absolute; top: 315px; left: 0; width: 100%;
    display: flex; justify-content: center; align-items: center; gap: 22px;
    transform: translateY(-100%);
  }
  .brand-dot {
    width: 78px; height: 78px; border-radius: 50%;
    background: var(--soft-white); flex: none;
  }
  .brand-name {
    font-weight: 600; font-size: 46px; letter-spacing: 0.5px;
    color: var(--soft-white); text-transform: uppercase; white-space: nowrap;
  }
  .front-web {
    position: absolute; bottom: 36px; width: 100%; text-align: center;
    color: var(--soft-white); font-size: 15px; font-weight: 400; letter-spacing: 0.3px;
  }

  .back-brand {
    position: absolute; top: 76px; left: 48px;
    display: flex; align-items: center; gap: 8px;
  }
  .back-brand .brand-dot { width: 26px; height: 26px; background: var(--brand-blue); }
  .back-brand .brand-name { font-size: 15px; color: var(--brand-blue); letter-spacing: 0.2px; }

  .person { position: absolute; top: 250px; left: 255px; }
  .person-name {
    font-weight: 700; font-size: 25px; color: var(--brand-blue); text-transform: uppercase;
    letter-spacing: 0.5px;
  }
  .person-title { font-size: 14px; color: var(--ink-grey); margin-top: 4px; padding-left: 46px; letter-spacing: 1px; }
  .person-rule { width: 231px; height: 1px; background: var(--rule-grey); margin: 14px 0 16px 0; }
  .contact-list { list-style: none; padding-left: 15px; }
  .contact-item {
    display: flex; align-items: center; gap: 12px;
    font-size: 15px; color: var(--ink-grey); margin-bottom: 12px;
  }
  .contact-icon { width: 18px; height: 18px; flex: none; }
</style>
</head>
<body>
<main class="canvas">
  <section class="card card-front" aria-label="Card front">
    <div class="front-brand">
      <span class="brand-dot"></span>
      <span class="brand-name">Ward Compass</span>
    </div>
    <p class="front-web">www.wardcompass.example</p>
  </section>

  <section class="card card-back" aria-label="Card back">
    <div class="back-brand">
      <span class="brand-dot"></span>
      <span class="brand-name">Ward Compass</span>
    </div>
    <div class="person">
      <h1 class="person-name">Salwa Kettani</h1>
      <p class="person-title">CEO</p>
      <div class="person-rule"></div>
      <ul class="contact-list">
        <li class="contact-item">
          <svg class="contact-icon" viewBox="0 0 18 18" aria-hidden="true">
            <circle cx="9" cy="9" r="9" fill="var(--brand-blue)"/>
            <path d="M6.2 4.6l1.5 1.6-.8 1.2c.5 1.1 1.4 2 2.5 2.5l1.2-.8 1.6 1.5-.7 1.4c-3.2-.2-6.4-3.4-6.6-6.6z" fill="#fff"/>
          </svg>
          <span>+90 612 348 2175</span>
        </li>
        <li class="contact-item">
          <svg class="contact-icon" viewBox="0 0 18 18" aria-hidden="true">
            <circle cx="9" cy="9" r="9" fill="var(--brand-blue)"/>
            <rect x="4.5" y="6" width="9" height="6.2" rx="0.6" fill="#fff"/>
            <path d="M4.8 6.3L9 9.4l4.2-3.1" fill="none" stroke="var(--brand-blue)" stroke-width="0.9"/>
          </svg>
          <span>info@wardcompass.example</span>
        </li>
      </ul>
    </div>
  </section>
</main>
</body>
</html>
```